Business Cards for new orthopaedic surgery practice

My husband and I are starting our own orthopaedic surgery practice. We are looking for a business card that is uniform, but one will have my name/title and the other will have his. You can just create one design with my name on it for now. But when I choose your design as the winning design I will ask that you add another copy with his name/title.

We are looking for classy, simple, elite all in one. We like dark blues/a little gold/yellow. Something that goes with our logo. We want our logo incorporated. Here is all the info you need:
Business name: RV Bone & Vitality Center
Location: 38517 North Willowmere Ave
Coral Springs, FL 33071
Phone: 954-218-4063
Fax: 954-582-7341
Email: info@myrvbonecare.example

Names: Lydia Vance, M.D.
Board Certified Hand and Upper Extremity Surgeon

Ebo Dansu, M.D.
Board Certified Hip & Knee Replacement/General Orthopaedic Surgeon

Can decide what you want to put on the back. Maybe a slogan:
Rooted in Care. Focused on You

I am just going to upload our logo. The only thing is if we select you as the winning design, the location, and phone numbers may change. We will need your help to update that once fully solidified.

Industry/Entity Type

Medical

Contact Information for Business Card

Colors
0054AA
0677BA
7BADD7
CADEEF
E8F1F8
0094D4
00A9DD
6FCCEA
C7EBF8
E9F6FB

Requirements
Must have
• class, appeal,
Should not have
• We want to air on the side of masculine if we are looking at masculine vs. feminine feel. But we still want it classy, sophisticated, and something we will love

```html
<!DOCTYPE html>
<html lang="en">
<head>
<meta charset="utf-8">
<title>RV Bone &amp; Vitality Center — Business Card</title>
<link href="https://fonts.googleapis.com/css2?family=Marcellus&family=EB+Garamond:wght@400;500&display=swap" rel="stylesheet">
<style>
  :root {
    --navy: #182a55;
    --gold: #b89244;
    --white: #ffffff;
    --ink: #1d2440;
    --backdrop: #e6e8ec;
    --photo-gold: #c29a4e;
    --photo-dark: #2a2a33;
  }
  * { box-sizing: border-box; margin: 0; padding: 0; }
  html, body { width: 1200px; height: 942px; overflow: hidden; }
  body {
    background: var(--backdrop);
    font-family: "EB Garamond", Georgia, serif;
    color: var(--ink);
    position: relative;
  }
  .card {
    position: absolute;
    left: 250px;
    width: 700px;
    height: 400px;
    background: var(--white);
    border-radius: 22px;
    overflow: hidden;
    box-shadow: 0 10px 30px rgba(20, 30, 60, 0.18);
  }
  .card--back { top: 52px; display: flex; }
  .card--front { top: 490px; }

  /* Back side */
  .brand-panel {
    width: 330px;
    height: 100%;
    background: var(--navy);
    display: flex;
    flex-direction: column;
    align-items: center;
    justify-content: center;
    gap: 22px;
  }
  .brand-mark {
    width: 46px; height: 46px;
    border: 2px solid var(--white);
    border-radius: 50%;
  }
  .brand-name {
    font-family: "Marcellus", Georgia, serif;
    color: var(--white);
    font-size: 26px;
    letter-spacing: 3px;
    text-transform: uppercase;
    text-align: center;
    line-height: 1.35;
  }
  .appointment {
    flex: 1;
    padding: 70px 44px 0 46px;
  }
  .appointment__title {
    font-family: "Marcellus", Georgia, serif;
    color: var(--gold);
    font-size: 22px;
    letter-spacing: 1px;
    text-transform: uppercase;
    margin-bottom: 34px;
  }
  .field {
    display: flex;
    align-items: flex-end;
    gap: 12px;
    margin-bottom: 26px;
    font-size: 17px;
    font-weight: 500;
  }
  .field__line { flex: 1; border-bottom: 1.5px solid var(--navy); height: 1px; }
  .weekdays { display: flex; gap: 22px; margin: 16px 0 22px; }
  .weekday {
    width: 38px; height: 38px;
    border: 2px solid var(--navy);
    box-shadow: 3px 3px 0 var(--navy);
    display: flex; align-items: center; justify-content: center;
    font-family: "Marcellus", Georgia, serif;
    font-size: 18px;
    color: var(--navy);
  }
  .closed-note {
    font-family: "Marcellus", Georgia, serif;
    color: var(--gold);
    font-size: 14px;
    letter-spacing: 0.5px;
    text-transform: uppercase;
  }

  /* Front side */
  .portrait {
    position: absolute;
    left: 70px; top: 80px;
    width: 220px; height: 220px;
  }
  .details {
    position: absolute;
    left: 340px; top: 48px;
    width: 320px;
  }
  .doctor-name {
    font-family: "Marcellus", Georgia, serif;
    color: var(--gold);
    font-size: 30px;
    letter-spacing: 1px;
    text-transform: uppercase;
    line-height: 1.1;
  }
  .doctor-title { font-size: 17px; line-height: 1.2; margin-top: 6px; }
  .rule { border: 0; border-top: 1.5px solid var(--gold); margin: 14px 0; }
  .contact { list-style: none; }
  .contact li {
    display: flex; align-items: center; gap: 12px;
    font-size: 17px; line-height: 1.45;
  }
  .contact svg { width: 14px; height: 14px; fill: var(--gold); flex: none; }
  .address { font-size: 17px; line-height: 1.25; }
  .practice-line {
    position: absolute;
    left: 0; right: 0; bottom: 30px;
    text-align: center;
    font-family: "Marcellus", Georgia, serif;
    color: var(--gold);
    font-size: 15px;
    letter-spacing: 5px;
    text-transform: uppercase;
  }
</style>
</head>
<body>

  <section class="card card--back" aria-label="Card back">
    <div class="brand-panel">
      <span class="brand-mark"></span>
      <p class="brand-name">RV Bone &amp;<br>Vitality Center</p>
    </div>
    <div class="appointment">
      <h2 class="appointment__title">Appointment with us</h2>
      <div class="field"><span>Date</span><span class="field__line"></span></div>
      <div class="field"><span>Time</span><span class="field__line"></span></div>
      <div class="weekdays">
        <span class="weekday">M</span>
        <span class="weekday">T</span>
        <span class="weekday">W</span>
        <span class="weekday">T</span>
        <span class="weekday">F</span>
      </div>
      <p class="closed-note">Saturday and Sunday closed</p>
    </div>
  </section>

  <section class="card card--front" aria-label="Card front">
    <svg class="portrait" viewBox="0 0 220 220">
      <path d="M18 150 A96 96 0 0 1 40 40" fill="none" stroke="var(--gold)" stroke-width="2.5"/>
      <path d="M180 40 A96 96 0 0 1 202 150" fill="none" stroke="var(--gold)" stroke-width="2.5"/>
      <defs>
        <linearGradient id="portraitFill" x1="0" y1="0" x2="0" y2="1">
          <stop offset="0" stop-color="var(--photo-gold)"/>
          <stop offset="1" stop-color="var(--photo-dark)"/>
        </linearGradient>
      </defs>
      <circle cx="110" cy="110" r="80" fill="url(#portraitFill)" stroke="var(--navy)" stroke-width="3"
              role="img" aria-label="Portrait photograph of the doctor"/>
    </svg>

    <div class="details">
      <h1 class="doctor-name">Lydia Vance, M.D.</h1>
      <p class="doctor-title">Board Certified Hand<br>and Upper Extremity Surgeon</p>
      <hr class="rule">
      <ul class="contact">
        <li><svg viewBox="0 0 16 16"><path d="M3 1l3 3-2 2c1 2 4 5 6 6l2-2 3 3-2 2C7 15 1 9 1 3z"/></svg>954-218-4063 (Phone)</li>
        <li><svg viewBox="0 0 16 16"><path d="M4 1h8v4H4zM1 6h14v7h-3v2H4v-2H1zM5 10v4h6v-4z"/></svg>954-582-7341 (Fax)</li>
        <li><svg viewBox="0 0 16 16"><path d="M1 3h14v10H1zM2 4l6 5 6-5v1L8 10 2 5z"/></svg>info@myrvbonecare.example</li>
      </ul>
      <hr class="rule">
      <p class="address">38517 North Willowmere Ave, Coral Springs,<br>FL 33071</p>
    </div>

    <p class="practice-line">Orthopaedic Surgery Practice</p>
  </section>

</body>
</html>
```